Harborline Outpost Registry needs a web design

We are launching a new website and need a web design. The website is going to list every military base and installment around the world with information on each base such as a description of the base, the history of the base, contact information at the base, address, lat/long of the base, and any other relevant information including images of the base. We need a home page with navigation menu and the design of the military base page so that every military base page is formatted the same for the referenced information. We have included an example of the content that may be found on the base page(s). We are also going to have the information available in spanish.

We also wanted to mention we will be building this website in wordpress.

We also wanted to note that in the format of each base page, we will have a frequently asked questions section with answers.

```html
<!DOCTYPE html>
<html lang="en">
<head>
<meta charset="utf-8">
<title>Harborline Outpost Registry</title>
<link rel="stylesheet" href="https://fonts.googleapis.com/css2?family=Exo+2:wght@400;600;700;800&family=Open+Sans:wght@400;600;700&display=swap">
<style>
:root{
  --red:#c8162f;
  --red-dark:#9e1024;
  --navy:#2e2b63;
  --navy-deep:#1f1d47;
  --ink:#141414;
  --text:#4a4a4a;
  --muted:#8a8a8a;
  --grey-bg:#f1f1f3;
  --panel:#e6e6e9;
  --black:#0b0b0e;
  --white:#fff;
  --gold:#f4b400;
}
*{box-sizing:border-box;margin:0;padding:0}
html,body{width:1200px;height:3096px;overflow:hidden}
body{font-family:"Open Sans",Arial,sans-serif;color:var(--text);background:var(--white);position:relative}
h1,h2,h3,h4,.display{font-family:"Exo 2",Arial,sans-serif}

/* top bar */
.topbar{height:36px;background:var(--red);color:var(--white);font-size:14px;font-weight:600;display:flex;align-items:center;justify-content:space-between;padding:0 24px}

/* hero */
.hero{position:relative;height:560px}
.hero-photo{position:absolute;inset:0;background:linear-gradient(160deg,#9fb6c8 0%,#5d7f9b 35%,#2e4d6b 70%,#1c3550 100%)}
.hero-shade{position:absolute;inset:0;background:linear-gradient(90deg,rgba(0,0,0,.05),rgba(10,25,45,.35))}
.nav{position:absolute;top:0;left:0;right:0;height:70px;display:flex;align-items:center;padding:0 24px;z-index:2}
.brand{font-family:"Exo 2",Arial,sans-serif;font-weight:700;font-size:22px;color:var(--white);flex:0 0 auto}
.menu{display:flex;gap:26px;list-style:none;margin-left:auto;margin-right:22px}
.menu li{color:var(--white);font-size:14px;font-weight:600}
.phone-btn{display:flex;align-items:center;background:var(--red);color:var(--white);font-size:14px;font-weight:600;height:34px;border-radius:3px;overflow:hidden}
.phone-btn .ico{width:34px;height:34px;background:var(--white);display:flex;align-items:center;justify-content:center}
.phone-btn span{padding:0 14px}
.lang{margin-left:12px;background:var(--navy);color:var(--white);font-size:13px;font-weight:700;height:34px;padding:0 12px;display:flex;align-items:center;gap:6px;border-radius:3px}
.hero-copy{position:absolute;right:100px;top:170px;text-align:right;color:var(--white)}
.hero-copy .kicker{font-family:"Exo 2",Arial,sans-serif;font-weight:700;font-size:38px;letter-spacing:1px}
.hero-copy h1{font-size:52px;font-weight:800;line-height:1.1}
.search{position:absolute;right:100px;top:330px;width:500px;height:52px;background:var(--white);border-radius:26px;display:flex;align-items:center;padding:0 6px 0 24px;font-size:15px;color:var(--text)}
.search .field{flex:1;display:flex;align-items:center;justify-content:space-between;padding-right:16px;border-right:1px solid #ddd;margin-right:16px}
.search .field:last-of-type{border-right:none}
.search .btn{background:var(--red);color:var(--white);height:40px;border-radius:20px;padding:0 18px;display:flex;align-items:center;gap:8px;font-weight:700}
.feature-band{position:absolute;left:0;right:0;bottom:60px;height:120px;background:rgba(20,20,25,.55);display:flex;justify-content:center;gap:110px;padding-top:18px}
.feature{text-align:center;color:var(--white);font-size:15px;font-weight:600}
.feature .ring{width:56px;height:56px;border:2px solid var(--white);border-radius:50%;margin:0 auto 10px;display:flex;align-items:center;justify-content:center}
.hero-curve{position:absolute;left:0;bottom:0;width:1200px;height:80px}

/* bases */
.bases{padding:110px 100px 0;height:720px}
.section-head{display:flex;justify-content:space-between;align-items:flex-start}
.title{font-size:30px;font-weight:800;color:var(--ink);text-transform:uppercase}
.title::after{content:"";display:block;width:60px;height:3px;background:var(--red);margin-top:12px}
.state-search{display:flex;align-items:center;gap:10px;margin-top:6px}
.state-search .input{width:260px;height:38px;border:1px solid #ddd;border-radius:3px;display:flex;align-items:center;padding:0 14px;font-size:14px;color:var(--muted)}
.state-search .btn{height:38px;background:var(--red);color:var(--white);padding:0 18px;display:flex;align-items:center;font-size:14px;font-weight:700;border-radius:3px}
.base-row{display:flex;justify-content:space-between;margin-top:50px;padding:0 10px}
.base{text-align:center;width:170px}
.base .photo{width:170px;height:170px;border-radius:50%;border:5px solid #eee;box-shadow:0 4px 10px rgba(0,0,0,.15)}
.base p{font-weight:700;color:var(--ink);font-size:15px;margin-top:16px}
.p1{background:linear-gradient(160deg,#d9a070,#7a5a40)}
.p2{background:linear-gradient(160deg,#c7ccd2,#4e5763)}
.p3{background:linear-gradient(160deg,#9fb592,#4e6a48)}
.p4{background:linear-gradient(160deg,#a7b7a0,#50603c)}
.p5{background:linear-gradient(160deg,#f3b055,#8a3f1a)}

/* popular */
.popular{padding:40px 100px 0;height:900px;display:flex;gap:50px;border-top:1px solid #eee}
.popular-main{flex:1}
.card{display:flex;gap:30px;margin-top:50px}
.card:first-of-type{margin-top:40px}
.card .photo{width:200px;height:200px;flex:0 0 200px;border-radius:4px}
.card h3{font-size:22px;font-weight:700;color:var(--ink);margin-top:10px}
.card .sub{font-size:14px;color:var(--ink);font-weight:600;margin:14px 0 8px}
.card p{font-size:13px;line-height:1.55}
.c1{background:linear-gradient(160deg,#f0a050,#3a2a20)}
.c2{background:linear-gradient(160deg,#b58a6a,#4e3d2e)}
.c3{background:linear-gradient(160deg,#8d8a80,#2d2b28)}
.reviews{width:290px;background:var(--panel);border-radius:6px;padding:20px 18px;margin-top:30px;height:720px}
.reviews h4{font-size:18px;font-weight:600;color:var(--ink);text-transform:uppercase;margin-bottom:16px}
.review{display:flex;align-items:center;gap:0;margin-bottom:20px}
.review .avatar{width:56px;height:56px;border-radius:50%;background:linear-gradient(160deg,#8a7a6a,#3a3028);border:3px solid var(--white);flex:0 0 56px;margin-right:-14px;position:relative;z-index:1}
.review .box{background:var(--navy);color:var(--white);border-radius:6px;padding:12px 12px 12px 24px;flex:1}
.review .name{font-weight:700;font-size:14px}
.review .stars{color:var(--gold);font-size:14px;letter-spacing:2px;margin:4px 0}
.review .msg{font-size:10px;line-height:1.4;opacity:.85}
.review .more{font-size:11px;margin-top:6px;font-weight:600}

/* countries */
.countries{background:var(--grey-bg);height:600px;padding:70px 100px 0;text-align:center;position:relative}
.countries h2{font-size:30px;font-weight:800;color:var(--ink);text-transform:uppercase;letter-spacing:1px}
.countries h2::after{content:"";display:block;width:60px;height:3px;background:var(--red);margin:12px auto 0}
.countries .intro{font-size:15px;line-height:1.6;margin:22px auto 0;width:520px}
.alphabet{display:flex;justify-content:space-between;margin-top:50px;font-size:17px;color:var(--ink);font-weight:600}
.alphabet .on{color:var(--red);text-decoration:underline}
.country-list{display:grid;grid-template-columns:repeat(3,1fr);text-align:left;margin-top:24px;row-gap:16px;width:680px}
.country-list span{color:var(--red);font-size:16px}
.country-list span::before{content:"» ";color:var(--muted)}
.footer-curve{position:absolute;left:0;bottom:0;width:1200px;height:80px}

/* footer */
.footer{background:var(--black);height:240px;color:#cfcfcf;display:flex;padding:50px 100px 0;gap:60px}
.footer h4{color:var(--white);font-size:15px;font-weight:700;text-transform:uppercase;margin-bottom:20px}
.f-about{width:260px}
.f-about .brand-small{font-family:"Exo 2",Arial,sans-serif;color:var(--white);font-size:18px;font-weight:700;margin-bottom:16px}
.f-about p{font-size:13px;line-height:1.6}
.f-links{width:150px}
.f-links li{list-style:none;font-size:13px;margin-bottom:12px}
.f-links li::before{content:"› ";color:var(--red)}
.f-contact{width:260px}
.f-contact .row{display:flex;gap:12px;font-size:13px;margin-bottom:14px;line-height:1.5}
.f-social{margin-left:auto}
.f-social .icons{display:flex;gap:10px}
.f-social .icons span{width:34px;height:34px;border-radius:50%;border:1px solid #777;display:block}
.bottom{background:var(--black);border-top:1px solid #2a2a2a;height:76px;color:#cfcfcf;font-size:13px;display:flex;align-items:center;justify-content:center}
</style>
</head>
<body>

<div class="topbar">
  <span>Address: Camp Alder Ridge, KY, United States</span>
  <span>Latitude: 36.4821</span>
  <span>N Longitude: -84.6310</span>
  <span>W DSN (555) 016-3732</span>
</div>

<header class="hero">
  <div class="hero-photo" role="img" aria-label="Aerial photo of an aircraft carrier at sea"></div>
  <div class="hero-shade"></div>
  <nav class="nav">
    <div class="brand">Harborline Outpost Registry</div>
    <ul class="menu"><li>Home</li><li>About Us</li><li>Products</li><li>Contact Us</li></ul>
    <div class="phone-btn">
      <div class="ico"><svg width="16" height="16" viewBox="0 0 24 24"><path fill="#c8162f" d="M6.6 10.8a15 15 0 0 0 6.6 6.6l2.2-2.2c.3-.3.7-.4 1-.2 1.1.4 2.3.6 3.6.6.6 0 1 .4 1 1V20c0 .6-.4 1-1 1A17 17 0 0 1 3 4c0-.6.4-1 1-1h3.5c.6 0 1 .4 1 1 0 1.3.2 2.5.6 3.6.1.3 0 .7-.2 1z"/></svg></div>
      <span>+1 (555) 014-2797</span>
    </div>
    <div class="lang">EN <svg width="10" height="6" viewBox="0 0 10 6"><path d="M0 0h10L5 6z" fill="#fff"/></svg></div>
  </nav>
  <div class="hero-copy">
    <div class="kicker">WELCOME TO</div>
    <h1>Harborline Outpost Registry</h1>
  </div>
  <div class="search">
    <div class="field">The Base title</div>
    <div class="field">Country <svg width="10" height="6" viewBox="0 0 10 6"><path d="M0 0h10L5 6z" fill="#888"/></svg></div>
    <div class="field">State <svg width="10" height="6" viewBox="0 0 10 6"><path d="M0 0h10L5 6z" fill="#888"/></svg></div>
    <div class="btn">Search <svg width="14" height="14" viewBox="0 0 24 24"><circle cx="10" cy="10" r="7" stroke="#fff" stroke-width="3" fill="none"/><path d="M15 15l6 6" stroke="#fff" stroke-width="3"/></svg></div>
  </div>
  <div class="feature-band">
    <div class="feature"><div class="ring"><svg width="26" height="26" viewBox="0 0 24 24"><path d="M12 2l8 4v6c0 5-3.5 9-8 10-4.5-1-8-5-8-10V6z" fill="none" stroke="#fff" stroke-width="1.8"/></svg></div>Nemo enim ipsam</div>
    <div class="feature"><div class="ring"><svg width="26" height="26" viewBox="0 0 24 24"><path d="M12 2a7 7 0 0 0-7 7c0 5 7 13 7 13s7-8 7-13a7 7 0 0 0-7-7z" fill="none" stroke="#fff" stroke-width="1.8"/><circle cx="12" cy="9" r="2.5" fill="#fff"/></svg></div>Nemo enim ipsam</div>
    <div class="feature"><div class="ring"><svg width="26" height="26" viewBox="0 0 24 24"><circle cx="12" cy="12" r="9" fill="none" stroke="#fff" stroke-width="1.8"/><path d="M7 12l3.5 3.5L17 9" fill="none" stroke="#fff" stroke-width="2"/></svg></div>Nemo enim ipsam</div>
  </div>
  <svg class="hero-curve" viewBox="0 0 1200 80" preserveAspectRatio="none"><path d="M0 20 Q600 100 1200 20 V80 H0z" fill="#2e2b63"/><path d="M0 40 Q600 110 1200 40 V80 H0z" fill="#fff"/></svg>
</header>

<section class="bases">
  <div class="section-head">
    <h2 class="title">Military Bases</h2>
    <div class="state-search"><div class="input">Search by State</div><div class="btn">Search</div></div>
  </div>
  <div class="base-row">
    <div class="base"><div class="photo p1" role="img" aria-label="Base entrance sign"></div><p>Nemo enim ipsam</p></div>
    <div class="base"><div class="photo p2" role="img" aria-label="Fighter jet on a runway"></div><p>Nemo enim ipsam</p></div>
    <div class="base"><div class="photo p3" role="img" aria-label="Aerial view of base grounds"></div><p>Nemo enim ipsam</p></div>
    <div class="base"><div class="photo p4" role="img" aria-label="Base buildings among trees"></div><p>Nemo enim ipsam</p></div>
    <div class="base"><div class="photo p5" role="img" aria-label="Aircraft at sunset"></div><p>Nemo enim ipsam</p></div>
  </div>
</section>

<section class="popular">
  <div class="popular-main">
    <h2 class="title">Popular This Week</h2>
    <article class="card">
      <div class="photo c1" role="img" aria-label="Jet aircraft silhouetted at dusk"></div>
      <div>
        <h3>Alder Ridge Outpost</h3>
        <div class="sub">Training grounds and armored units</div>
        <p>A large installation set in rolling hills, home to training ranges, armored units and support commands. The base supports thousands of service members and families with housing, schools and medical care. Visitors can find gate hours, contact numbers and history notes on the full base page.</p>
      </div>
    </article>
    <article class="card">
      <div class="photo c2" role="img" aria-label="Soldier in uniform beside a flag"></div>
      <div>
        <h3>Alder Ridge Outpost</h3>
        <div class="sub">Training grounds and armored units</div>
        <p>A large installation set in rolling hills, home to training ranges, armored units and support commands. The base supports thousands of service members and families with housing, schools and medical care. Visitors can find gate hours, contact numbers and history notes on the full base page.</p>
      </div>
    </article>
    <article class="card">
      <div class="photo c3" role="img" aria-label="Service member saluting"></div>
      <div>
        <h3>Alder Ridge Outpost</h3>
        <div class="sub">Training grounds and armored units</div>
        <p>A large installation set in rolling hills, home to training ranges, armored units and support commands. The base supports thousands of service members and families with housing, schools and medical care. Visitors can find gate hours, contact numbers and history notes on the full base page.</p>
      </div>
    </article>
  </div>
  <aside class="reviews">
    <h4>Recent Reviews</h4>
    <div class="review"><div class="avatar" role="img" aria-label="Reviewer portrait"></div><div class="box"><div class="name">Daniel Moreno</div><div class="stars">★★★★★</div><div class="msg">Clear gate hours and contacts helped our family visit go smoothly.</div><div class="more">Continue Reading...</div></div></div>
    <div class="review"><div class="avatar" role="img" aria-label="Reviewer portrait"></div><div class="box"><div class="name">Grace Holloway</div><div class="stars">★★★★★</div><div class="msg">Clear gate hours and contacts helped our family visit go smoothly.</div><div class="more">Continue Reading...</div></div></div>
    <div class="review"><div class="avatar" role="img" aria-label="Reviewer portrait"></div><div class="box"><div class="name">Marcus Bell</div><div class="stars">★★★★★</div><div class="msg">Clear gate hours and contacts helped our family visit go smoothly.</div><div class="more">Continue Reading...</div></div></div>
    <div class="review"><div class="avatar" role="img" aria-label="Reviewer portrait"></div><div class="box"><div class="name">Lena Ortiz</div><div class="stars">★★★★★</div><div class="msg">Clear gate hours and contacts helped our family visit go smoothly.</div><div class="more">Continue Reading...</div></div></div>
  </aside>
</section>

<section class="countries">
  <h2>Find Military Bases by Country</h2>
  <p class="intro">Browse installations worldwide by country, then open any base for its full details, history and contacts.</p>
  <div class="alphabet">
    <span>A</span><span>B</span><span>C</span><span>D</span><span>E</span><span>F</span><span>G</span><span>H</span><span>I</span><span>J</span><span>K</span><span>L</span><span>M</span><span>N</span><span>O</span><span>P</span><span>Q</span><span>R</span><span>S</span><span>T</span><span class="on">U</span><span>V</span><span>W</span><span>X</span><span>Y</span><span>Z</span>
  </div>
  <div class="country-list">
    <span>United States of America</span><span>Ukraine</span><span>Uruguay</span>
    <span>United Kingdom</span><span>Uzbekistan</span><span></span>
    <span>Uganda</span><span>United Arab Emirates</span>
  </div>
  <svg class="footer-curve" viewBox="0 0 1200 80" preserveAspectRatio="none"><path d="M0 80 Q600 -10 1200 80z" fill="#2e2b63"/><path d="M0 80 Q600 20 1200 80z" fill="#0b0b0e"/></svg>
</section>

<footer>
  <div class="footer">
    <div class="f-about">
      <div class="brand-small">Harborline Outpost Registry</div>
      <p>A directory of bases worldwide, with history, contacts, locations and visitor details for each installation.</p>
    </div>
    <div class="f-links">
      <h4>Quicklinks</h4>
      <ul><li>Home</li><li>About Us</li><li>Products</li><li>Contact Us</li></ul>
    </div>
    <div class="f-contact">
      <h4>Contact Us</h4>
      <div class="row"><svg width="14" height="18" viewBox="0 0 24 30"><path d="M12 0a11 11 0 0 0-11 11c0 8 11 19 11 19s11-11 11-19A11 11 0 0 0 12 0z" fill="#fff"/></svg><span>Camp Alder Ridge, KY,<br>United States</span></div>
      <div class="row"><svg width="14" height="14" viewBox="0 0 24 24"><path fill="#fff" d="M6.6 10.8a15 15 0 0 0 6.6 6.6l2.2-2.2c.3-.3.7-.4 1-.2 1.1.4 2.3.6 3.6.6.6 0 1 .4 1 1V20c0 .6-.4 1-1 1A17 17 0 0 1 3 4c0-.6.4-1 1-1h3.5c.6 0 1 .4 1 1 0 1.3.2 2.5.6 3.6.1.3 0 .7-.2 1z"/></svg><span>+1 (555) 014-2797</span></div>
      <div class="row"><svg width="16" height="12" viewBox="0 0 24 18"><rect x="1" y="1" width="22" height="16" fill="none" stroke="#fff" stroke-width="2"/><path d="M1 1l11 9 11-9" fill="none" stroke="#fff" stroke-width="2"/></svg><span>info@harborlineregistry.example</span></div>
    </div>
    <div class="f-social">
      <h4>Social Media</h4>
      <div class="icons"><span></span><span></span><span></span><span></span></div>
    </div>
  </div>
  <div class="bottom">© copyrights 2023 · Harborline Outpost Registry | All Rights Reserved</div>
</footer>

</body>
</html>
```